Web design required

1-We need a web design for existing company based in New Zealand
2-We build residential house and light commercial
3-We has in-house designer which allow us can provide interior design
4-We modeling project before site construction, which enable both client and construction team to visually analysis whole project,

Target Market(s)

middle class residential house market
Ref: http://www.parvellbuilders.co.nz/

Industry/Entity Type

Construction Company

Number of Pages Required

1 page

Font styles to use
Sans Serif
Other font styles liked:
• Such as : Central Gothic or similar which has more design taste

Colors

Designer to choose colors to be used in the design.

Requirements
Must have
• Front sheet, contact information, sample project

```html
<!DOCTYPE html>
<html lang="en">
<head>
<meta charset="utf-8">
<title>Kestrel Homes</title>
<link href="https://fonts.googleapis.com/css2?family=Open+Sans:wght@400;600;700&family=Poppins:wght@300;500;600&display=swap" rel="stylesheet">
<style>
:root{
  --blue:#0762a8;
  --blue-dark:#054f89;
  --ink:#4a4a4a;
  --muted:#777;
  --white:#fff;
}
*{box-sizing:border-box;margin:0;padding:0}
html,body{width:1200px;height:2970px;overflow:hidden}
body{position:relative;font-family:"Open Sans",Arial,sans-serif;color:var(--ink);background:var(--white)}
.abs{position:absolute}
.heading{font-family:"Poppins",Arial,sans-serif;font-weight:600}

/* hero */
.hero{left:0;top:0;width:1200px;height:1016px;background:linear-gradient(135deg,#3b3d40 0%,#2a2c2f 45%,#4a4a46 100%)}
.hero-photo{left:0;top:0;width:1200px;height:770px;background:radial-gradient(ellipse at 20% 20%,rgba(160,140,40,.35),transparent 45%),radial-gradient(ellipse at 80% 30%,rgba(200,200,200,.18),transparent 55%)}
.nav{left:0;top:0;width:1200px;height:64px;border-bottom:1px solid rgba(255,255,255,.25);display:flex;justify-content:center;gap:44px;align-items:center}
.nav a{color:var(--white);text-decoration:none;font-size:16px;letter-spacing:.3px}
.hero-shape{left:0;top:0}
.brand{left:0;width:1200px;text-align:center;color:var(--white);font-family:"Poppins",Arial,sans-serif;font-weight:500}
.brand-top{top:395px;font-size:72px;letter-spacing:18px}
.brand-bottom{top:470px;font-size:44px;letter-spacing:44px}
.welcome-title{left:80px;top:780px;font-size:40px;color:var(--white)}
.welcome-text{left:80px;top:838px;width:600px;font-size:14.5px;line-height:25px;color:var(--white)}
.tools{left:703px;top:782px;width:465px;height:178px;border-radius:8px;background:linear-gradient(90deg,#c9a12a,#e8c640 35%,#8a6d3c 65%,#5a4a3a)}

/* services */
.section-title{left:0;width:1200px;text-align:center;font-size:40px;color:var(--ink)}
.service{width:520px;height:126px}
.service svg{position:absolute;left:0;top:0}
.service h3{position:absolute;left:133px;top:10px;font-family:"Poppins",Arial,sans-serif;font-weight:500;font-size:24px;color:var(--blue)}
.service p{position:absolute;left:133px;top:48px;width:340px;font-size:15px;line-height:25px;color:var(--muted)}
.service a{position:absolute;left:133px;top:98px;font-size:15px;font-weight:700;color:var(--blue);text-decoration:none}

/* projects */
.projects{left:0;top:1499px;width:1200px;height:626px;background:var(--blue)}
.projects .section-title{color:var(--white);top:40px}
.filter{top:101px;height:38px;border:1.5px solid var(--white);border-radius:19px;color:var(--white);font-size:16px;display:flex;align-items:center;justify-content:center}
.filter.active{background:var(--white);color:var(--ink)}
.shot{border:2px solid rgba(255,255,255,.5)}
.view-more{left:517px;top:536px;width:166px;height:40px;border-radius:20px;background:var(--white);color:var(--ink);font-size:17px;display:flex;align-items:center;justify-content:center}

/* news */
.news{z-index:2}
.news-photo{width:208px;height:141px}
.news-title{font-size:15px;font-weight:700;color:var(--blue)}
.news-date{font-size:15px;color:var(--muted);display:flex;align-items:center;gap:8px}
.news-text{width:290px;font-size:15px;line-height:24px;color:var(--muted)}

/* footer */
.footer{left:0;top:2390px;width:1200px;height:528px;background:linear-gradient(160deg,#3a3b3e,#262729 60%,#3a2e28)}
.footer-shape{left:0;top:2390px}
.foot-brand{left:79px;width:208px;text-align:center;color:var(--white);font-family:"Poppins",Arial,sans-serif;font-weight:500}
.foot-head{font-family:"Poppins",Arial,sans-serif;font-weight:300;font-size:22px;color:var(--white)}
.foot-link{font-size:15px;color:var(--white)}
.field{left:620px;width:233px;height:40px;border:1.5px solid var(--white);color:var(--white);font-size:15px;padding:7px 6px}
.subscribe{left:620px;top:2816px;width:138px;height:39px;background:var(--white);color:var(--blue-dark);font-weight:700;font-size:17px;display:flex;align-items:center;justify-content:center}
.contact{left:893px;display:flex;gap:14px;color:var(--white);font-size:15px;line-height:22px}
.contact svg{flex:none;margin-top:3px}
.copyright{left:0;top:2918px;width:1200px;height:52px;background:var(--blue);color:var(--white);font-size:15px;display:flex;align-items:center;justify-content:center}
</style>
</head>
<body>

<section class="abs hero">
  <div class="abs hero-photo" role="img" aria-label="Photo of a hard hat, blueprints and tape measure on a desk, darkened"></div>
  <nav class="abs nav">
    <a href="#">HOME</a><a href="#">ABOUT</a><a href="#">SERVICES</a><a href="#">PROJECTS</a><a href="#">NEWS</a><a href="#">CONTACT</a>
  </nav>
  <div class="abs brand brand-top">KESTREL</div>
  <div class="abs brand brand-bottom">HOMES</div>
  <svg class="abs hero-shape" width="1200" height="1016" viewBox="0 0 1200 1016">
    <polygon points="0,538 712,728 1200,505 1200,512 712,736 0,546" fill="#d9d9d9"/>
    <polygon points="0,546 712,736 1200,512 1200,1016 0,1016" fill="#0762a8"/>
    <polygon points="0,546 712,736 1200,512 1200,530 712,762 0,552" fill="#8d8d8d"/>
  </svg>
  <h1 class="abs heading welcome-title">Welcome To KESTREL HOMES</h1>
  <p class="abs welcome-text">Lorem Ipsum is simply dummy text of the printing and typesetting industry. Lorem Ipsum has been the industry's standard dummy text ever since the 1500s, when an unknown printer took a galley of type and scrambled it to make a type specimen book. It has survived not only five centuries, but also the leap into electronic typesetting, remaining essentially unchanged.</p>
  <div class="abs tools" role="img" aria-label="Photo of a yellow hard hat with a leather tool belt, level and hammer"></div>
</section>

<h2 class="abs heading section-title" style="top:1050px">Our Services</h2>

<div class="abs service" style="left:79px;top:1133px">
  <svg width="106" height="126" viewBox="0 0 106 126"><polygon points="53,2 104,32 104,94 53,124 2,94 2,32" fill="none" stroke="#0762a8" stroke-width="2"/><polygon points="53,10 96,36 96,90 53,116 10,90 10,36" fill="none" stroke="#0762a8" stroke-width="1"/><path d="M53 46 L31 64 H37 V82 H49 V70 H57 V82 H69 V64 H75 Z" fill="#0762a8"/></svg>
  <h3>Service 1</h3><p>Lorem Ipsum is simply dummy text of the printing and typesetting industry.</p><a href="#">READ MORE</a>
</div>
<div class="abs service" style="left:624px;top:1133px">
  <svg width="106" height="126" viewBox="0 0 106 126"><polygon points="53,2 104,32 104,94 53,124 2,94 2,32" fill="none" stroke="#0762a8" stroke-width="2"/><polygon points="53,10 96,36 96,90 53,116 10,90 10,36" fill="none" stroke="#0762a8" stroke-width="1"/><path d="M39 48 H59 V56 H67 V82 H39 Z" fill="#0762a8"/><g fill="#fff"><rect x="43" y="53" width="4" height="4"/><rect x="51" y="53" width="4" height="4"/><rect x="43" y="61" width="4" height="4"/><rect x="51" y="61" width="4" height="4"/><rect x="59" y="61" width="4" height="4"/><rect x="43" y="69" width="4" height="4"/><rect x="51" y="69" width="4" height="4"/><rect x="59" y="69" width="4" height="4"/></g></svg>
  <h3>Service 2</h3><p>Lorem Ipsum is simply dummy text of the printing and typesetting industry.</p><a href="#">READ MORE</a>
</div>
<div class="abs service" style="left:79px;top:1301px">
  <svg width="106" height="126" viewBox="0 0 106 126"><polygon points="53,2 104,32 104,94 53,124 2,94 2,32" fill="none" stroke="#0762a8" stroke-width="2"/><polygon points="53,10 96,36 96,90 53,116 10,90 10,36" fill="none" stroke="#0762a8" stroke-width="1"/><path d="M53 46 L31 64 H37 V82 H49 V70 H57 V82 H69 V64 H75 Z" fill="#0762a8"/></svg>
  <h3>Service 3</h3><p>Lorem Ipsum is simply dummy text of the printing and typesetting industry.</p><a href="#">READ MORE</a>
</div>
<div class="abs service" style="left:624px;top:1301px">
  <svg width="106" height="126" viewBox="0 0 106 126"><polygon points="53,2 104,32 104,94 53,124 2,94 2,32" fill="none" stroke="#0762a8" stroke-width="2"/><polygon points="53,10 96,36 96,90 53,116 10,90 10,36" fill="none" stroke="#0762a8" stroke-width="1"/><path d="M39 48 H59 V56 H67 V82 H39 Z" fill="#0762a8"/><g fill="#fff"><rect x="43" y="53" width="4" height="4"/><rect x="51" y="53" width="4" height="4"/><rect x="43" y="61" width="4" height="4"/><rect x="51" y="61" width="4" height="4"/><rect x="59" y="61" width="4" height="4"/><rect x="43" y="69" width="4" height="4"/><rect x="51" y="69" width="4" height="4"/><rect x="59" y="69" width="4" height="4"/></g></svg>
  <h3>Service 4</h3><p>Lorem Ipsum is simply dummy text of the printing and typesetting industry.</p><a href="#">READ MORE</a>
</div>

<section class="abs projects">
  <h2 class="abs heading section-title">Projects</h2>
  <div class="abs filter" style="left:354px;width:159px">Commecial</div>
  <div class="abs filter" style="left:523px;width:156px">Residential</div>
  <div class="abs filter active" style="left:689px;width:156px">All</div>

  <div class="abs shot" style="left:77px;top:158px;width:244px;height:137px;background:linear-gradient(135deg,#d8cfc2,#9a8a78)" role="img" aria-label="Project photo: bedroom interior"></div>
  <div class="abs shot" style="left:77px;top:319px;width:244px;height:182px;background:linear-gradient(135deg,#e6ebee,#a8b4b8)" role="img" aria-label="Project photo: bright living room"></div>
  <div class="abs shot" style="left:345px;top:158px;width:243px;height:113px;background:linear-gradient(135deg,#eceae6,#8e8a84)" role="img" aria-label="Project photo: open-plan dining area"></div>
  <div class="abs shot" style="left:345px;top:295px;width:243px;height:206px;background:linear-gradient(160deg,#d9cbb6,#8c7a66)" role="img" aria-label="Project photo: curved modern building exterior"></div>
  <div class="abs shot" style="left:610px;top:158px;width:243px;height:180px;background:linear-gradient(160deg,#cfd9e2,#6e7d6a)" role="img" aria-label="Project photo: modern house exterior with garden"></div>
  <div class="abs shot" style="left:610px;top:362px;width:243px;height:139px;background:linear-gradient(135deg,#f0eeea,#b5aea4)" role="img" aria-label="Project photo: white kitchen interior"></div>
  <div class="abs shot" style="left:877px;top:158px;width:244px;height:141px;background:linear-gradient(135deg,#8da59a,#c9ced0)" role="img" aria-label="Project photo: architectural detail"></div>
  <div class="abs shot" style="left:877px;top:323px;width:244px;height:178px;background:linear-gradient(135deg,#b9b4ac,#ecebe8)" role="img" aria-label="Project photo: minimalist living space"></div>

  <div class="abs view-more">VIEW MORE</div>
</section>

<h2 class="abs heading section-title" style="top:2157px">Latest News</h2>

<div class="abs news news-photo" style="left:77px;top:2231px;background:linear-gradient(135deg,#8fb1d0,#c48a4a)" role="img" aria-label="News photo: builders reviewing plans on site"></div>
<div class="abs news news-title" style="left:309px;top:2236px">Lorem Ipsum is simply dummy</div>
<div class="abs news news-date" style="left:309px;top:2264px"><svg width="14" height="14" viewBox="0 0 14 14"><rect x="1" y="2.5" width="12" height="10.5" fill="none" stroke="#777" stroke-width="1.3"/><line x1="1" y1="6" x2="13" y2="6" stroke="#777" stroke-width="1.3"/><line x1="4" y1="1" x2="4" y2="4" stroke="#777" stroke-width="1.3"/><line x1="10" y1="1" x2="10" y2="4" stroke="#777" stroke-width="1.3"/></svg>April 06, 2017</div>
<p class="abs news news-text" style="left:309px;top:2290px">Lorem Ipsum is simply dummy text of the printing and typesetting industry.</p>

<div class="abs news news-photo" style="left:626px;top:2231px;background:linear-gradient(135deg,#a9c8e2,#5d84a8)" role="img" aria-label="News photo: construction workers on a building site"></div>
<div class="abs news news-title" style="left:857px;top:2236px">Lorem Ipsum is simply dummy</div>
<div class="abs news news-date" style="left:857px;top:2264px"><svg width="14" height="14" viewBox="0 0 14 14"><rect x="1" y="2.5" width="12" height="10.5" fill="none" stroke="#777" stroke-width="1.3"/><line x1="1" y1="6" x2="13" y2="6" stroke="#777" stroke-width="1.3"/><line x1="4" y1="1" x2="4" y2="4" stroke="#777" stroke-width="1.3"/><line x1="10" y1="1" x2="10" y2="4" stroke="#777" stroke-width="1.3"/></svg>April 06, 2017</div>
<p class="abs news news-text" style="left:857px;top:2290px">Lorem Ipsum is simply dummy text of the printing and typesetting industry.</p>

<footer>
  <div class="abs footer" role="img" aria-label="Darkened photo of a construction site with hard hats"></div>
  <svg class="abs footer-shape" width="1200" height="280" viewBox="0 0 1200 280">
    <polygon points="0,0 1200,0 1200,4 712,222 0,20" fill="#fff"/>
    <polygon points="0,20 712,222 1200,4 1200,32 712,256 0,48" fill="#0762a8"/>
  </svg>

  <div class="abs foot-brand" style="top:2780px;font-size:36px;letter-spacing:5px">KESTREL</div>
  <div class="abs foot-brand" style="top:2826px;font-size:22px;letter-spacing:14px">HOMES</div>

  <div class="abs foot-head" style="left:350px;top:2662px">Useful Links</div>
  <div class="abs foot-link" style="left:350px;top:2708px">Home</div>
  <div class="abs foot-link" style="left:350px;top:2741px">About</div>
  <div class="abs foot-link" style="left:350px;top:2775px">Services</div>
  <div class="abs foot-link" style="left:350px;top:2809px">Project</div>
  <div class="abs foot-link" style="left:473px;top:2708px">News</div>
  <div class="abs foot-link" style="left:473px;top:2741px">Contact</div>

  <div class="abs foot-head" style="left:622px;top:2662px">Newsletter</div>
  <div class="abs field" style="top:2709px">Enter Name</div>
  <div class="abs field" style="top:2762px">Enter Email</div>
  <div class="abs subscribe">SUBSCRIBE</div>

  <div class="abs foot-head" style="left:893px;top:2662px">Get In Touch With Us</div>
  <div class="abs contact" style="top:2700px"><svg width="14" height="18" viewBox="0 0 14 18"><path d="M7 0C3.1 0 0 3 0 6.8 0 11.8 7 18 7 18s7-6.2 7-11.2C14 3 10.9 0 7 0zm0 9.3A2.6 2.6 0 1 1 7 4a2.6 2.6 0 0 1 0 5.3z" fill="#fff"/></svg><span>14 Harbour Lane, Tauranga<br>Bay of Plenty 3110</span></div>
  <div class="abs contact" style="top:2752px"><svg width="16" height="16" viewBox="0 0 16 16"><path d="M3.5 0.5l2.6 3.3-1.5 2c1 2.2 2.7 3.9 4.9 4.9l2-1.5 3.3 2.6-1.6 2.8C7.4 14.5 1.3 8.4 0.7 2.1z" fill="#fff"/></svg><span>07 555 0148</span></div>
  <div class="abs contact" style="top:2784px"><svg width="16" height="14" viewBox="0 0 16 14"><rect x="1" y="1.5" width="14" height="11" fill="none" stroke="#fff" stroke-width="1.5"/><path d="M1 2l7 6 7-6" fill="none" stroke="#fff" stroke-width="1.5"/></svg><span>info@kestrelhomes.com</span></div>

  <div class="abs copyright">2017 ©KESTREL HOMES. - All Rights Reserved.</div>
</footer>

</body>
</html>
```